IT Company requires new Business Card design.

Over the years we have had a few different business card designs. We are now due for new cards across the board for all staff. We felt this would be a good time to start fresh with a new design. Our traditional card simply had our details on the front, and a list of services on the back. We don't particularly need the list of services, we have had cards where the only thing on the rear of the card was our logo.
Feel free to be creative, we would like our tag line "Complete IT Management" to appear at some point, doesn't necessarily have to be with the logo.
I have attached samples and drafts of various previous cards we have used over the years.

```html
<!DOCTYPE html>
<html lang="en">
<head>
<meta charset="utf-8">
<title>Ridgeway Systems – Business Card</title>
<link rel="stylesheet" href="https://fonts.googleapis.com/css2?family=Source+Sans+3:wght@400;600;700&display=swap">
<style>
  :root {
    --backdrop: #e6e4e1;
    --card: #ffffff;
    --brand: #5f6b77;
    --ink: #3b4148;
    --ink-soft: #555b62;
    --edge: #d6d3cf;
  }
  * { margin: 0; padding: 0; box-sizing: border-box; }
  html, body { width: 1034px; height: 1200px; overflow: hidden; }
  body {
    background: var(--backdrop);
    font-family: "Source Sans 3", "Helvetica Neue", Arial, sans-serif;
    color: var(--ink);
    position: relative;
  }
  .card {
    position: absolute;
    left: 75px;
    width: 897px;
    height: 512px;
    background: var(--card);
    border: 1px solid var(--edge);
    box-shadow: 0 2px 8px rgba(0,0,0,0.12);
  }
  .card--front { top: 69px; }
  .card--back { top: 628px; }

  .brand-name {
    font-weight: 700;
    color: var(--brand);
    text-transform: uppercase;
    line-height: 0.9;
  }
  .card--front .brand-name {
    position: absolute;
    left: 68px;
    top: 20px;
  }
  .brand-name .line-1 { display: block; font-size: 62px; letter-spacing: 1px; }
  .brand-name .line-2 { display: block; font-size: 36px; letter-spacing: 1.5px; margin-top: 4px; }

  .person {
    position: absolute;
    left: 68px;
    top: 158px;
  }
  .person__name { font-size: 28px; font-weight: 600; color: var(--ink-soft); line-height: 1.2; }
  .person__role { font-size: 22px; color: var(--ink-soft); line-height: 1.3; }

  .contact-list {
    position: absolute;
    left: 68px;
    top: 236px;
    list-style: none;
  }
  .contact-list li {
    display: flex;
    align-items: center;
    height: 35.5px;
    font-size: 22px;
    color: var(--ink);
  }
  .contact-list svg { width: 18px; height: 18px; margin-right: 12px; fill: var(--ink-soft); flex: none; }

  .address {
    position: absolute;
    left: 68px;
    top: 424px;
    font-size: 22px;
    line-height: 1.4;
    color: var(--ink);
  }

  .brand-square {
    position: absolute;
    left: 572px;
    top: 82px;
    width: 256px;
    height: 256px;
    background: var(--brand);
  }
  .tagline {
    position: absolute;
    left: 517px;
    top: 432px;
    width: 330px;
    font-size: 17px;
    letter-spacing: 3.4px;
    text-transform: uppercase;
    color: var(--brand);
    text-align: center;
    white-space: nowrap;
  }

  .back-lockup {
    position: absolute;
    left: 0;
    right: 0;
    top: 168px;
    display: flex;
    align-items: center;
    justify-content: center;
    gap: 28px;
  }
  .back-lockup .brand-square--small {
    width: 150px;
    height: 150px;
    background: var(--brand);
  }
  .back-lockup .brand-name .line-1 { font-size: 64px; }
  .back-lockup .brand-name .line-2 { font-size: 40px; }

  .web-address {
    position: absolute;
    left: 0;
    right: 0;
    top: 452px;
    text-align: center;
    font-size: 25px;
    letter-spacing: 2px;
    color: var(--ink);
  }
</style>
</head>
<body>

<section class="card card--front">
  <div class="brand-name">
    <span class="line-1">Ridgeway</span>
    <span class="line-2">Systems</span>
  </div>

  <div class="person">
    <p class="person__name">Marcus Reid</p>
    <p class="person__role">Operation Manager</p>
  </div>

  <ul class="contact-list">
    <li>
      <svg viewBox="0 0 24 24" aria-hidden="true"><path d="M6.6 10.8a15.1 15.1 0 0 0 6.6 6.6l2.2-2.2a1 1 0 0 1 1-.25 11.4 11.4 0 0 0 3.6.57 1 1 0 0 1 1 1V20a1 1 0 0 1-1 1A17 17 0 0 1 3 4a1 1 0 0 1 1-1h3.5a1 1 0 0 1 1 1c0 1.25.2 2.45.57 3.57a1 1 0 0 1-.25 1z"/></svg>
      08 5550 1480
    </li>
    <li>
      <svg viewBox="0 0 24 24" aria-hidden="true"><path d="M7 1h10a2 2 0 0 1 2 2v18a2 2 0 0 1-2 2H7a2 2 0 0 1-2-2V3a2 2 0 0 1 2-2zm0 3v11h10V4zm5 14a1.5 1.5 0 1 0 0 3 1.5 1.5 0 0 0 0-3z"/></svg>
      0400 555 218
    </li>
    <li>
      <svg viewBox="0 0 24 24" aria-hidden="true"><path d="M6 2h9l3 3v4h1a3 3 0 0 1 3 3v8H2v-8a3 3 0 0 1 3-3h1zm2 2v5h8V6h-2V4zM5 14v2h3v-2zm5 0v2h3v-2zm5 0v2h3v-2z"/></svg>
      08 5550 1481
    </li>
    <li>
      <svg viewBox="0 0 24 24" aria-hidden="true"><path d="M2 5h20v14H2zm2 2v.4l8 5.2 8-5.2V7zm0 2.8V17h16V9.8l-8 5.2z"/></svg>
      marcus@ridgewaysystems.com.au
    </li>
    <li>
      <svg viewBox="0 0 24 24" aria-hidden="true"><path d="M12 2a10 10 0 1 0 0 20 10 10 0 0 0 0-20zm6.9 9h-3a15 15 0 0 0-1.3-6A8 8 0 0 1 18.9 11zM12 4.1c.9 1.3 1.7 3.7 1.9 6.9h-3.8c.2-3.2 1-5.6 1.9-6.9zM9.4 5a15 15 0 0 0-1.3 6h-3A8 8 0 0 1 9.4 5zM5.1 13h3a15 15 0 0 0 1.3 6 8 8 0 0 1-4.3-6zm6.9 6.9c-.9-1.3-1.7-3.7-1.9-6.9h3.8c-.2 3.2-1 5.6-1.9 6.9zm2.6-.9a15 15 0 0 0 1.3-6h3a8 8 0 0 1-4.3 6z"/></svg>
      www.ridgewaysystems.com.au
    </li>
  </ul>

  <address class="address" style="font-style: normal;">
    Unit 4 12 Kestrel Road<br>
    Harmony WA 6999
  </address>

  <div class="brand-square" aria-hidden="true"></div>
  <p class="tagline">Complete IT Management</p>
</section>

<section class="card card--back">
  <div class="back-lockup">
    <div class="brand-square--small" aria-hidden="true"></div>
    <div class="brand-name">
      <span class="line-1">Ridgeway</span>
      <span class="line-2">Systems</span>
    </div>
  </div>
  <p class="web-address">www.ridgewaysystems.com.au</p>
</section>

</body>
</html>
```